SaaS Early tech startup business card design

Unique design for experience ecommerce platform company. the business cards will be used by executive members. conformance with color code is required.

```html
<!DOCTYPE html>
<html lang="en">
<head>
<meta charset="utf-8">
<title>Novra — Business Card</title>
<link rel="stylesheet" href="https://fonts.googleapis.com/css2?family=Montserrat:wght@500;700&family=Arimo:wght@400&display=swap">
<style>
  :root {
    --stage: #0f0f10;
    --card: #2a2b2d;
    --edge: #1fb89a;
    --teal: #1fb89a;
    --blue: #1a6fa8;
    --text: #e4e6e8;
    --muted: #b9bcc0;
    --rule: #4a4c50;
  }
  * { box-sizing: border-box; margin: 0; padding: 0; }
  html, body {
    width: 1200px;
    height: 820px;
    overflow: hidden;
    background: var(--stage);
  }
  .canvas {
    position: relative;
    width: 1200px;
    height: 820px;
    display: flex;
    align-items: center;
    justify-content: center;
    gap: 60px;
  }
  .card {
    position: relative;
    width: 520px;
    height: 300px;
    background: var(--card);
    border-bottom: 4px solid var(--edge);
    border-left: 2px solid var(--edge);
    overflow: hidden;
  }
  .brand-name {
    position: absolute;
    font-family: "Montserrat", sans-serif;
    font-weight: 700;
    color: var(--teal);
    letter-spacing: 0.01em;
    line-height: 1;
  }
  .card-front .brand-name { top: 48px; right: 40px; font-size: 66px; }
  .divider {
    position: absolute;
    top: 150px;
    left: 190px;
    right: 22px;
    height: 1px;
    background: linear-gradient(90deg, transparent, var(--rule) 20%, var(--rule) 80%, transparent);
  }
  .person {
    position: absolute;
    left: 40px;
    top: 168px;
    font-family: "Montserrat", sans-serif;
  }
  .person-name {
    font-size: 20px;
    font-weight: 500;
    color: var(--teal);
    letter-spacing: 0.01em;
    white-space: nowrap;
  }
  .person-title {
    font-family: "Arimo", sans-serif;
    font-size: 14px;
    color: var(--text);
    margin-top: 2px;
  }
  .contact-list {
    position: absolute;
    left: 40px;
    top: 222px;
    list-style: none;
    font-family: "Arimo", sans-serif;
    font-size: 14px;
    color: var(--text);
  }
  .contact-item {
    display: flex;
    align-items: center;
    gap: 8px;
    height: 20px;
    white-space: nowrap;
  }
  .contact-icon { width: 13px; height: 13px; flex: none; }
  .accent { color: var(--teal); }
  .address {
    position: absolute;
    right: 40px;
    top: 170px;
    text-align: right;
    font-family: "Arimo", sans-serif;
    font-style: normal;
    font-size: 13px;
    line-height: 1.4;
    color: var(--muted);
    white-space: nowrap;
  }
  .card-back { border-bottom-width: 6px; }
  .card-back .brand-name { top: 112px; right: 34px; font-size: 62px; }
  .emblem-field {
    position: absolute;
    left: 40px;
    top: 36px;
    width: 270px;
    height: 230px;
    border-radius: 40px;
    background: radial-gradient(ellipse at 40% 40%, rgba(26,111,168,0.35), rgba(31,184,154,0.22) 55%, transparent 75%);
  }
</style>
</head>
<body>
<main class="canvas">
  <section class="card card-front" aria-label="Card front">
    <div class="brand-name">novra</div>
    <div class="divider"></div>
    <div class="person">
      <div class="person-name">DANIEL REYES</div>
      <div class="person-title">Managing Director</div>
    </div>
    <ul class="contact-list">
      <li class="contact-item">
        <svg class="contact-icon" viewBox="0 0 16 16" aria-hidden="true"><path fill="var(--teal)" d="M3.6 1.2l2.2 2.6-1.2 1.6c.9 2 2.4 3.5 4.4 4.4l1.6-1.2 2.6 2.2-1.1 2.6C7 13.2 2.8 9 1.9 2.3z"/></svg>
        <span>021-987 654 320</span>
      </li>
      <li class="contact-item">
        <svg class="contact-icon" viewBox="0 0 16 16" aria-hidden="true"><rect x="1" y="3" width="14" height="10" fill="var(--teal)"/><path d="M1 3l7 6 7-6" fill="none" stroke="var(--card)" stroke-width="1.4"/></svg>
        <span>hello@novralabs.com</span>
      </li>
      <li class="contact-item">
        <svg class="contact-icon" viewBox="0 0 16 16" aria-hidden="true"><g fill="none" stroke="var(--teal)" stroke-width="1.4"><circle cx="8" cy="8" r="6.5"/><ellipse cx="8" cy="8" rx="3" ry="6.5"/><path d="M1.5 8h13M2.5 4.8h11M2.5 11.2h11"/></g></svg>
        <span>www.<span class="accent">novralabs</span>.com</span>
      </li>
    </ul>
    <address class="address">17 Linden Row, Suite 210<br>60314, Eastland</address>
  </section>

  <section class="card card-back" aria-label="Card back">
    <div class="emblem-field" role="img" aria-label="Large looping line-art brand motif in blue and teal"></div>
    <div class="brand-name">novra</div>
  </section>
</main>
</body>
</html>
```